Brandwyn Fuel Retro Website Design

Have a logo. Need a website design to go along with the logo design. Full Design Specs are here: https://files.plinverdocs.net/sheet/d/8QmRtZxWv3-41pk527LNB_XY4HaPcOdsuw2K-rb6/view

Target Market(s)

Independent Gas Station Owners

Number of Pages Required

1 page

Font styles to use
Sans Serif

Colors

Designer to choose colors to be used in the design.

```html
<!DOCTYPE html>
<html lang="en">
<head>
<meta charset="utf-8">
<title>Brandwyn Fuel</title>
<link rel="stylesheet" href="https://fonts.googleapis.com/css2?family=Roboto+Slab:wght@400;700&family=Roboto:wght@400;500&display=swap">
<style>
:root{
  --paper:#f4efe9;
  --ink:#5b5758;
  --ink-dark:#4a4748;
  --red:#e02227;
  --red-dark:#b9181d;
  --footer:#4d4b4c;
  --white:#ffffff;
}
*{margin:0;padding:0;box-sizing:border-box}
html,body{width:1200px;height:3758px;overflow:hidden}
body{background:var(--paper);color:var(--ink);font-family:"Roboto",sans-serif;position:relative}
.abs{position:absolute}
.slab{font-family:"Roboto Slab",serif}

.brand{left:0;width:1200px;display:flex;flex-direction:column;align-items:center;gap:6px}
.brand-dot{width:44px;height:44px;border-radius:50%;background:var(--red)}
.brand-name{font-family:"Roboto Slab",serif;font-weight:700;font-size:22px;color:var(--ink-dark);letter-spacing:.5px}

.nav{left:0;width:1200px;display:flex;justify-content:center;gap:38px;font-family:"Roboto Slab",serif;font-size:15px;color:var(--ink)}
.nav a{color:inherit;text-decoration:none;padding:4px 24px;border-radius:14px}
.nav a:first-child{margin-left:-40px}
.nav .active{background:var(--red);color:var(--white);font-weight:700}

.btn{display:inline-flex;align-items:center;justify-content:center;background:var(--red);color:var(--white);font-family:"Roboto Slab",serif;font-weight:700;font-size:16px;border-radius:10px;box-shadow:0 3px 0 var(--red-dark);text-transform:uppercase}

.hero-title{left:0;width:1200px;top:278px;text-align:center;font-family:"Roboto Slab",serif;font-weight:700;font-size:60px;color:var(--ink);letter-spacing:1px}
.hero-text{left:200px;width:800px;top:356px;text-align:center;font-size:18px;line-height:27px;font-weight:500;color:var(--ink)}
.hero-photo{left:0;top:470px;width:1200px;height:640px;background:linear-gradient(to bottom,rgba(244,239,233,1) 0%,rgba(150,145,138,.55) 25%,#8b8680 55%,#6f6b66 80%,rgba(244,239,233,1) 100%)}

.section-title{font-family:"Roboto Slab",serif;font-weight:700;font-size:52px;color:var(--ink)}
.section-text{font-size:17.5px;line-height:30px;color:var(--ink)}

.circle-photo{left:92px;top:988px;width:452px;height:452px;border-radius:50%;border:8px solid #d2cdc8;background:radial-gradient(circle at 60% 40%,#b9b6b0,#5e5c58 70%,#3c3a38)}
.tank-photo-large{left:665px;top:1493px;width:446px;height:430px;border-radius:28px 28px 28px 60px;border:5px solid var(--white);background:linear-gradient(to bottom,#6f6c66 0%,#a6a39c 35%,#d9d8d4 55%,#8d8a84 100%);box-shadow:0 6px 14px rgba(0,0,0,.15)}
.tank-photo-small{left:636px;top:1786px;width:188px;height:182px;border-radius:16px;border:5px solid var(--white);background:linear-gradient(to bottom,#7a776f,#e3e2de 55%,#c9c7c2);box-shadow:0 8px 18px rgba(0,0,0,.25)}

.farm-band{left:0;top:2057px;width:1200px;height:521px;background:linear-gradient(to right,#9c9890 0%,#a9a59d 35%,#6e6c69 60%,#4e4d4c 80%,#5a5958 100%)}
.farm-title{color:var(--white)}
.farm-text{color:var(--white)}

.container-photo{left:191px;top:2923px;width:819px;height:387px;border-radius:60px 60px 60px 60px / 40px 40px 40px 40px;border:7px solid var(--white);background:linear-gradient(to bottom,#e5e5e6 0%,#d5d6d8 30%,#8e9196 55%,#7b7e83 80%,#cfcfcf 100%)}

.footer{left:0;top:3404px;width:1200px;height:354px;background:var(--footer)}
.footer .brand-name{color:var(--white)}
.footer-nav{color:var(--white);font-weight:700}
.copyright{left:0;width:1200px;top:3654px;text-align:center;color:var(--white);font-family:"Roboto Slab",serif;font-weight:700;font-size:15px}
.to-top{left:1123px;top:3651px;width:40px;height:40px;border-radius:50%;background:var(--red)}
</style>
</head>
<body>

<header>
  <div class="abs brand" style="top:22px">
    <span class="brand-dot"></span>
    <span class="brand-name">Brandwyn Fuel</span>
  </div>
  <nav class="abs nav" style="top:138px">
    <a class="active">Home</a><a>Our Company</a><a>Products &amp; Services</a><a>Contact Us</a><a>B's Containers</a><a>Employment Opportunities</a>
  </nav>
</header>

<section class="hero">
  <div class="abs hero-photo" role="img" aria-label="Vintage sepia photo of a fuel depot with old delivery trucks and storage tanks"></div>
  <h1 class="abs hero-title">WELCOME TO BRANDWYN FUEL</h1>
  <p class="abs hero-text">Brandwyn Fuel provides the full-scale service of a petroleum distributor, delivering gasoline, diesel and lube oils to retail, commercial and farm accounts.</p>
  <a class="abs btn" style="left:513px;top:427px;width:172px;height:44px;font-size:19px">Read More</a>
</section>

<section class="fuel-delivery">
  <div class="abs circle-photo" role="img" aria-label="Fuel delivery truck parked under a loading rack"></div>
  <h2 class="abs section-title" style="left:605px;top:1098px">Fuel Delivery</h2>
  <p class="abs section-text" style="left:605px;top:1176px;width:520px">Brandwyn Fuel provides fuel delivery for independent gas stations, convenience stores, construction sites or any other commercial need.&nbsp; If you are looking for gasoline, high sulfer diesel fuel, farm diesel or other bulk fuel delivered to your business, we will take care of you!</p>
  <a class="abs btn" style="left:605px;top:1346px;width:146px;height:38px">Read More</a>
</section>

<section class="oil">
  <h2 class="abs section-title" style="left:87px;top:1578px">Oil</h2>
  <p class="abs section-text" style="left:87px;top:1657px;width:530px">Looking for speciality auto, tractor, tractor trailer, aviation or other commercial oils and lubricants Brandwyn Fuel can help!&nbsp; Just call one of our customer oriented staff and we will get what you need quick!&nbsp; We have a complete line of aviation oils and lubricants as well as gear lubricants, greases, oils and more!</p>
  <a class="abs btn" style="left:90px;top:1825px;width:146px;height:38px">Read More</a>
  <div class="abs tank-photo-large" role="img" aria-label="Large white and grey storage tanks in a gravel yard"></div>
  <div class="abs tank-photo-small" role="img" aria-label="Two white storage tanks"></div>
</section>

<section class="farm-fuel">
  <div class="abs farm-band" role="img" aria-label="Man at a diesel pump with two dogs"></div>
  <h2 class="abs section-title farm-title" style="left:607px;top:2206px">Farm Fuel</h2>
  <p class="abs section-text farm-text" style="left:605px;top:2284px;width:510px">Looking for gasoline, diesel red diesel off road fuel or farm diesel?&nbsp; We can deliver straight to your farm!&nbsp; We can setup your farm tanks, take care of EPA containment and deliver fuel when you need it!</p>
  <a class="abs btn" style="left:605px;top:2420px;width:146px;height:38px">Read More</a>
</section>

<section class="cargo">
  <h2 class="abs section-title" style="left:0;width:1200px;text-align:center;top:2668px">Cargo Containers</h2>
  <p class="abs section-text" style="left:200px;width:800px;text-align:center;top:2740px">Want to purchase or lease a storage container, we have what you need!<br>We can deliver or move storage containers to your home, business, construction site or any you need one!</p>
  <a class="abs btn" style="left:526px;top:2850px;width:148px;height:38px">Read More</a>
  <div class="abs container-photo" role="img" aria-label="Grey steel shipping container on a lot"></div>
</section>

<footer class="abs footer">
  <div class="abs brand" style="top:78px">
    <span class="brand-dot"></span>
    <span class="brand-name">Brandwyn Fuel</span>
  </div>
</footer>
<nav class="abs nav footer-nav" style="top:3614px">
  <a>Home</a><a>Our Company</a><a>Products &amp; Services</a><a>Contact Us</a><a>B's Containers</a><a>Employment Opportunities</a>
</nav>
<p class="abs copyright">Copyright 2019 | All Right Reserved</p>
<a class="abs to-top" aria-label="Back to top">
  <svg width="40" height="40" viewBox="0 0 40 40"><path d="M16 22 L20 18 L24 22" fill="none" stroke="#fff" stroke-width="2"/></svg>
</a>

</body>
</html>
```